Torvane Email Signature Banners – Fabrication Capability Series

www.Torvane.com.au is an Australian engineering and fabrication company specialising in fabrication and welding of :
steel piping spools,
skids and frames,
small volume process steel tanks
and general steel fabrication
We require four distinct banner designs for use in Microsoft Lintaro email signatures. Each banner will highlight a specific capability while maintaining a consistent brand identity.
Deliverables
Four banners total:
Piping Spools Fabrication – focus on precision welding and stainless steel pipework
Skid & Frames Fabrication – highlight skid systems and structural frames
Small Steel Tanks Fabrication – show fabricated tanks and workshop craftsmanship
General Fabrication Solutions – broad steel fabrication theme for company-wide use
Dimensions: 600–700 px wide × 100 px high
Format: PNG (preferred), small file size prefered
Resolution: 72 dpi
Background: non-transparent, industrial or workshop setting
Text examples:
1. Piping Spools Fabrication
Option A: “Expert Fabrication Solutions for Process Piping”
Option B: “Precision Welding for Complex Systems”
Option C: “Delivering Quality in Every Spool”
Option D: “Engineered for Flow, Built for Strength”
2. Skid & Frames Fabrication
Option A: “Custom Engineered Modular Systems”
Option B: “Built Strong. Designed Smart.”
Option C: “Reliable Frames for Industrial Performance”
Option D: “Modular Fabrication for Seamless Integration”
3. Small Steel Tanks Fabrication
Option A: “Precision Built for Your Needs”
Option B: “Compact Strength. Proven Durability.”
Option C: “Fabricated for Performance and Longevity”
Option D: “Small Tanks. Big Reliability.”
4. General Fabrication Solutions
Option A: “Quality Craftsmanship, Proven Results”
Option B: “Your Partner in Precision Fabrication”
Option C: “Engineering Excellence in Every Weld”
Option D: “Australian Fabrication. Global Standards.”
Style Direction
Clean, professional, and engineering‑focused
Use Torvane brand colours
Blend photo realism with vector clarity (no heavy gradients)
Include subtle industrial textures or workshop imagery
Typography: bold sans‑serif, legible at small scale
Usage Context
These banners will appear at the bottom of staff email signatures via Lintaro Email Signature Tool for Microsoft 365, so clarity and fast loading are essential. No Logo is required in the banners.
Reference
Existing Torvane signature is attached. Colour palette to match the signature style and logo.
Target Market(s)
Engineering and construction companies,
Industry/Entity Type
Engineering fabrication design
Look and feel

```html
<!DOCTYPE html>
<html lang="en">
<head>
<meta charset="utf-8">
<title>Fabrication Capability Banners</title>
<link rel="stylesheet" href="https://fonts.googleapis.com/css2?family=Poppins:wght@500;600;700;800&display=swap">
<style>
  :root {
    --page: #ffffff;
    --brand-blue: #163f96;
    --brand-blue-deep: #0f347f;
    --accent-cyan: #2ba9e1;
    --text-light: #ffffff;
    --photo-steel: #7d7f7c;
    --photo-ground: #8a8375;
    --workshop-dark: #0e1c28;
    --workshop-mid: #1d3443;
  }
  * { margin: 0; padding: 0; box-sizing: border-box; }
  html, body {
    width: 1200px; height: 388px; overflow: hidden;
    background: var(--page);
    font-family: "Poppins", sans-serif;
  }
  .canvas { position: relative; width: 1200px; height: 388px; }

  /* Banner: tanks */
  .banner { position: absolute; left: 17px; width: 1166px; overflow: hidden; }
  .banner--tanks { top: 17px; height: 164px; background: var(--brand-blue); }
  .tanks-photo-a {
    position: absolute; left: 0; top: 0; width: 145px; height: 100%;
    background: linear-gradient(160deg, #9a9a96 0%, #5e5f5c 55%, #3f3f3d 100%);
  }
  .tanks-photo-b {
    position: absolute; left: 145px; top: 0; width: 220px; height: 100%;
    background: linear-gradient(180deg, #a6a8a5 0%, var(--photo-steel) 45%, var(--photo-ground) 100%);
  }
  .tanks-panel {
    position: absolute; left: 365px; top: 0; right: 0; bottom: 0;
    background: linear-gradient(90deg, var(--brand-blue-deep), var(--brand-blue));
  }
  .tanks-title {
    position: absolute; left: 365px; right: 0; top: 28px;
    text-align: center; font-weight: 800; font-size: 50px; line-height: 1;
    color: var(--text-light); letter-spacing: -0.3px; white-space: nowrap;
  }
  .accent { color: var(--accent-cyan); }
  .tanks-tagline {
    position: absolute; left: 365px; right: 0; top: 94px;
    display: flex; justify-content: center; align-items: center; gap: 10px;
    font-weight: 600; font-size: 29px; line-height: 1; color: var(--text-light);
    white-space: nowrap;
  }
  .stripes { width: 50px; height: 16px; flex: none; }

  /* Banner: general */
  .banner--general { top: 200px; height: 163px; }
  .general-photo {
    position: absolute; inset: 0;
    background:
      radial-gradient(ellipse 260px 120px at 420px 60px, rgba(176,101,46,0.55), transparent 70%),
      radial-gradient(ellipse 300px 140px at 1000px 90px, rgba(60,110,140,0.45), transparent 70%),
      linear-gradient(90deg, var(--workshop-dark), var(--workshop-mid) 50%, var(--workshop-dark));
  }
  .general-title {
    position: absolute; left: 0; right: 0; top: 28px;
    text-align: center; font-weight: 800; font-size: 51px; line-height: 1;
    color: var(--accent-cyan); letter-spacing: -0.3px; white-space: nowrap;
  }
  .general-tagline {
    position: absolute; left: 61px; right: 70px; top: 96px;
    display: flex; align-items: center; gap: 14px;
    font-weight: 500; font-size: 30px; line-height: 1; color: var(--text-light);
    white-space: nowrap;
  }
  .rule { flex: 1; height: 2px; background: var(--text-light); }
</style>
</head>
<body>
<main class="canvas">
  <section class="banner banner--tanks">
    <div class="tanks-photo-a" role="img" aria-label="Close-up of a fabricated steel pipe end with flange"></div>
    <div class="tanks-photo-b" role="img" aria-label="Fabricated steel pipe spools laid out on a gravel yard"></div>
    <div class="tanks-panel"></div>
    <h2 class="tanks-title">Small Steel <span class="accent">Tanks Fabrication</span></h2>
    <p class="tanks-tagline">
      <svg class="stripes" viewBox="0 0 50 16" aria-hidden="true">
        <rect x="7" y="1" width="43" height="3" fill="#fff"/>
        <rect x="3.5" y="7" width="43" height="3" fill="#fff"/>
        <rect x="0" y="13" width="43" height="3" fill="#fff"/>
      </svg>
      Fabricated for Performance and Longevity
      <svg class="stripes" viewBox="0 0 50 16" aria-hidden="true">
        <rect x="7" y="1" width="43" height="3" fill="#fff"/>
        <rect x="3.5" y="7" width="43" height="3" fill="#fff"/>
        <rect x="0" y="13" width="43" height="3" fill="#fff"/>
      </svg>
    </p>
  </section>

  <section class="banner banner--general">
    <div class="general-photo" role="img" aria-label="Dark workshop scene with welding sparks flying"></div>
    <h2 class="general-title">General Fabrication Solutions</h2>
    <p class="general-tagline">
      <span class="rule"></span>
      Quality Craftsmanship, Proven Results
      <span class="rule"></span>
    </p>
  </section>
</main>
</body>
</html>
```